Emergency Dental Referral Company

I need a brochure to advertise my business to prospective dentists that may want to join or to dentists that may want to use this for their own patients. I also need to advertise this brochure to ER physicians who see many dental emergencies. This brochure is meant to be dual purpose: advertise our company and services to the ER physicians who then hand out the brochures to the dental emergency patients in pain. See our website for further details at www.vellumcrestora.com

I will also be attaching our logo design.

Target Market(s)

Emergency Room physicians and other medical personnel who will distribute these brochures to patients in dental pain and dental emergencies

Industry/Entity Type

Business

Font styles to use
Serif
Sans Serif

Requirements
Must have
• Must be simple! Must have a call to action- inspiration to go to website. Highlight our guarantee that states "If you are not seen by a dentist in 24 hours or less, you will receive your money back. Emphasis on the logo. Must discuss how we find a dentist in your zip code in three easy steps.
• For the color- please make similar to our website of www.vellumcrestora.com
Nice to have
• Would like to state that this service can see patients at any hour of the day.
Should not have
• no contact information besides the URL. www.vellumcrestora.com

```html
<!DOCTYPE html>
<html lang="en">
<head>
<meta charset="utf-8">
<title>Vellum Crestora – Emergency Dentist Brochure</title>
<link href="https://fonts.googleapis.com/css2?family=Open+Sans:wght@400;600;700;800&family=Merriweather+Sans:wght@400;700&display=swap" rel="stylesheet">
<style>
  :root{
    --green:#4bb649;
    --green-light:#6cc66a;
    --blue:#2a6db5;
    --blue-dark:#1f5597;
    --white:#ffffff;
    --ink:#2b8a6a;
    --grey:#5b5b5b;
    --page:#e4e4e4;
    --photo-a:#f3efe9;
    --photo-b:#e3c9b2;
  }
  *{box-sizing:border-box;margin:0;padding:0}
  html,body{width:1033px;height:1200px;overflow:hidden;background:var(--page);font-family:"Open Sans",sans-serif}
  .spread{position:absolute;left:20px;width:993px;height:570px;display:flex;background:var(--white);box-shadow:0 2px 8px rgba(0,0,0,.18);overflow:hidden}
  .spread--outside{top:20px}
  .spread--inside{top:610px}
  .panel{position:relative;width:331px;height:100%}
  .spread-art{position:absolute;inset:0;width:993px;height:570px}

  /* outside: steps panel */
  .panel--steps{background:var(--green);color:var(--white);padding:26px 22px}
  .steps-title{position:relative;height:150px}
  .steps-title__num{position:absolute;left:0;top:-12px;font-size:150px;font-weight:800;line-height:1}
  .steps-title__lead{position:absolute;left:92px;top:4px;font-size:27px;font-weight:600}
  .steps-title__box{position:absolute;left:84px;top:42px;background:var(--blue);padding:4px 12px;font-size:38px;font-weight:600;line-height:1.1;border-radius:4px}
  .step{display:flex;align-items:center;margin-top:14px}
  .step__num{width:50px;height:50px;border-radius:50%;background:var(--blue);border:3px solid var(--white);display:flex;align-items:center;justify-content:center;font-size:26px;font-weight:800;z-index:1;flex:none}
  .step__pill{margin-left:-14px;flex:1;height:40px;background:var(--white);border-radius:0 20px 20px 0;display:flex;align-items:center;padding-left:26px;color:var(--green);font-size:14px}
  .step__pill svg{flex:none;margin-right:18px}
  .step__label{flex:1;text-align:center;line-height:1.15}
  .shield{display:block;margin:22px auto 0}
  .guarantee-note{text-align:center;font-size:14px;line-height:1.4;margin-top:14px}

  /* outside: back panel */
  .panel--back{background:transparent}
  .brand{display:flex;align-items:center;gap:8px;font-family:"Open Sans",sans-serif;font-weight:700;color:var(--blue)}
  .brand__dot{width:16px;height:16px;border-radius:50%;background:var(--green);flex:none}
  .panel--back .brand{position:absolute;left:26px;top:36px;font-size:22px}
  .hour-badge{position:absolute;left:22px;top:370px;width:62px;height:80px;border:3px solid var(--white);border-radius:6px;color:var(--white);display:flex;flex-direction:column;align-items:center;justify-content:center;font-weight:800;font-size:22px;line-height:1}
  .hour-badge small{font-size:9px;font-weight:700;margin-top:4px}
  .back-url{position:absolute;left:26px;bottom:28px;color:var(--white);font-size:14px}

  /* outside: cover panel */
  .panel--cover{text-align:center}
  .cover-title{padding-top:14px;line-height:1.05}
  .cover-title__your{display:block;color:var(--blue);font-size:30px;font-weight:700}
  .cover-title__emergency{display:block;color:var(--green);font-size:30px;font-weight:700}
  .cover-title__dentist{display:block;color:var(--blue);font-size:38px;font-weight:800}
  .panel--cover .brand{position:absolute;left:40px;top:450px;font-size:30px}
  .cover-url{position:absolute;left:0;right:0;top:520px;color:var(--blue);font-size:15px;font-weight:700}

  /* inside: mission panel */
  .panel--mission{padding:26px 26px 0 24px;color:var(--ink);font-family:"Merriweather Sans",sans-serif;font-size:12.5px;line-height:1.3;text-align:center}
  .panel--mission p{margin-bottom:10px}
  .panel--mission .emphasis{color:var(--blue);font-weight:700;font-size:14px}
  .panel--mission .brand{position:absolute;left:24px;bottom:30px;font-size:22px}

  /* inside: services panels */
  .services{position:relative;width:662px;height:100%;background:var(--green)}
  .person{position:absolute;left:30px;top:70px;width:120px;height:410px;border-radius:50px 50px 6px 6px}
  .services__head{position:absolute;left:160px;top:28px;width:320px;color:var(--white);font-size:16px;text-align:center;line-height:1.3}
  .services .shield{position:absolute;right:40px;top:14px;margin:0}
  .symptoms{position:absolute;left:170px;top:118px;width:450px;list-style:none}
  .symptom{display:flex;align-items:center;height:34px;margin-bottom:13px;background:var(--white);border-radius:17px;color:var(--green);font-size:15px;font-weight:600}
  .symptom__icon{width:38px;height:38px;border-radius:50%;background:var(--blue);border:2px solid var(--white);display:flex;align-items:center;justify-content:center;margin:0 10px 0 -4px;flex:none}
  .service-band{position:absolute;left:-110px;right:0;bottom:40px;height:40px;background:var(--blue);color:var(--white);font-size:19px;font-weight:700;letter-spacing:.5px;display:flex;align-items:center;justify-content:center}
  .service-band-under{position:absolute;left:0;right:0;bottom:0;height:40px;background:var(--green-light)}
</style>
</head>
<body>

<!-- Outside of the trifold -->
<section class="spread spread--outside">
  <svg class="spread-art" viewBox="0 0 993 570" aria-hidden="true">
    <defs>
      <linearGradient id="photoTone" x1="0" y1="0" x2="1" y2="1">
        <stop offset="0" stop-color="#f3efe9"/>
        <stop offset="1" stop-color="#e0c4aa"/>
      </linearGradient>
    </defs>
    <polygon points="331,340 662,430 662,570 331,570" fill="#4bb649"/>
    <polygon points="331,330 662,420 662,432 331,342" fill="#2a6db5"/>
  </svg>

  <div class="panel panel--steps">
    <div class="steps-title">
      <span class="steps-title__num">3</span>
      <span class="steps-title__lead">STEPS TO</span>
      <span class="steps-title__box">DENTAL<br>CARE</span>
    </div>
    <div class="step">
      <span class="step__num">1</span>
      <span class="step__pill">
        <svg width="26" height="26" viewBox="0 0 26 26"><rect x="4" y="2" width="16" height="22" fill="none" stroke="#2a6db5" stroke-width="2"/><path d="M8 8h8M8 13h8M8 18h5" stroke="#2a6db5" stroke-width="2"/></svg>
        <span class="step__label">Fill out<br>Form</span>
      </span>
    </div>
    <div class="step">
      <span class="step__num">2</span>
      <span class="step__pill">
        <svg width="26" height="26" viewBox="0 0 26 26"><circle cx="11" cy="11" r="7" fill="none" stroke="#2a6db5" stroke-width="2.5"/><path d="M16 16l7 7" stroke="#2a6db5" stroke-width="3"/></svg>
        <span class="step__label">Find A<br>Dentist</span>
      </span>
    </div>
    <div class="step">
      <span class="step__num">3</span>
      <span class="step__pill">
        <svg width="26" height="26" viewBox="0 0 26 26"><rect x="3" y="5" width="20" height="18" rx="2" fill="none" stroke="#2a6db5" stroke-width="2"/><path d="M3 10h20M8 2v5M18 2v5" stroke="#2a6db5" stroke-width="2"/></svg>
        <span class="step__label">Get<br>Appointment</span>
      </span>
    </div>
    <svg class="shield" width="110" height="90" viewBox="0 0 110 90" aria-label="Money back guarantee">
      <path d="M55 4 L98 16 Q98 62 55 86 Q12 62 12 16 Z" fill="#2a6db5" stroke="#ffffff" stroke-width="3"/>
      <rect x="2" y="26" width="106" height="18" fill="#ffffff"/>
      <text x="55" y="39" text-anchor="middle" font-family="Open Sans, sans-serif" font-weight="800" font-size="12" fill="#2a6db5">GUARANTEE</text>
      <text x="55" y="62" text-anchor="middle" font-family="Open Sans, sans-serif" font-weight="800" font-size="16" fill="#ffffff">100%</text>
      <text x="55" y="74" text-anchor="middle" font-family="Open Sans, sans-serif" font-weight="700" font-size="8" fill="#ffffff">MONEY BACK</text>
    </svg>
    <p class="guarantee-note">If you are not seen by a dentist<br>in 24 hours or less, you will<br>receive your money back</p>
  </div>

  <div class="panel panel--back">
    <div class="brand"><span class="brand__dot"></span>Vellum Crestora</div>
    <div class="hour-badge">24<small>HOUR SERVICE</small></div>
    <span class="back-url">www.vellumcrestora.com</span>
  </div>

  <div class="panel panel--cover">
    <h1 class="cover-title">
      <span class="cover-title__your">Your</span>
      <span class="cover-title__emergency">Emergency</span>
      <span class="cover-title__dentist">DENTIST</span>
    </h1>
    <div class="brand"><span class="brand__dot"></span>Vellum Crestora</div>
    <span class="cover-url">www.vellumcrestora.com</span>
  </div>

  <svg style="position:absolute;left:331px;top:0" width="662" height="570" viewBox="331 0 662 570" role="img" aria-label="Photo of a smiling mother with two young children">
    <polygon points="331,110 662,110 662,150 993,150 993,430 662,420 331,330" fill="url(#photoTone)"/>
  </svg>
</section>

<!-- Inside of the trifold -->
<section class="spread spread--inside">
  <div class="panel panel--mission">
    <p>Our mission plain and simple is to get you seen by a qualified dentist as quickly as possible to get you out of pain.</p>
    <p>Nobody likes pain and no one should have to live with it. If we can get you seen by a dentist in 24 hours or less, we have succeeded.</p>
    <p class="emphasis">What we strive for is a quicker, more reliable method for patients to access their dental professional.</p>
    <p>Going to the local hospitals' Emergency Department for a tooth ache will not solve the issue, hospitals are often times not equipped to handle dental emergencies and do not have dentists on staff. You leave with antibiotics and pain medication, not a solution to the real underlying problem. Leave here confident, knowing you will see a dentist in less than 24 hours!</p>
    <div class="brand"><span class="brand__dot"></span>Vellum Crestora</div>
  </div>

  <div class="services">
    <div class="service-band-under"></div>
    <svg class="person" viewBox="0 0 120 410" preserveAspectRatio="none" role="img" aria-label="Photo of a smiling professional woman pointing to the list">
      <defs>
        <linearGradient id="personTone" x1="0" y1="0" x2="0" y2="1">
          <stop offset="0" stop-color="#d9d4cf"/>
          <stop offset="1" stop-color="#2c2a2a"/>
        </linearGradient>
      </defs>
      <rect width="120" height="410" rx="40" fill="url(#personTone)"/>
    </svg>
    <p class="services__head">If you are not seen by a dentist<br>in 24 hours or less, you will<br>receive your money back</p>
    <svg class="shield" width="100" height="80" viewBox="0 0 110 90" aria-label="Money back guarantee">
      <path d="M55 4 L98 16 Q98 62 55 86 Q12 62 12 16 Z" fill="#2a6db5" stroke="#ffffff" stroke-width="3"/>
      <rect x="2" y="26" width="106" height="18" fill="#ffffff"/>
      <text x="55" y="39" text-anchor="middle" font-family="Open Sans, sans-serif" font-weight="800" font-size="12" fill="#2a6db5">GUARANTEE</text>
      <text x="55" y="62" text-anchor="middle" font-family="Open Sans, sans-serif" font-weight="800" font-size="16" fill="#ffffff">100%</text>
      <text x="55" y="74" text-anchor="middle" font-family="Open Sans, sans-serif" font-weight="700" font-size="8" fill="#ffffff">MONEY BACK</text>
    </svg>
    <ul class="symptoms">
      <li class="symptom"><span class="symptom__icon"><svg width="16" height="16" viewBox="0 0 16 16"><path d="M2 8l4 4 8-9" fill="none" stroke="#fff" stroke-width="2.5"/></svg></span>Broken or Fractured Filling</li>
      <li class="symptom"><span class="symptom__icon"><svg width="16" height="16" viewBox="0 0 16 16"><path d="M2 8l4 4 8-9" fill="none" stroke="#fff" stroke-width="2.5"/></svg></span>Broken or Fractured Teeth</li>
      <li class="symptom"><span class="symptom__icon"><svg width="16" height="16" viewBox="0 0 16 16"><path d="M2 8l4 4 8-9" fill="none" stroke="#fff" stroke-width="2.5"/></svg></span>Discolored or Odd Looking Teeth</li>
      <li class="symptom"><span class="symptom__icon"><svg width="16" height="16" viewBox="0 0 16 16"><path d="M2 8l4 4 8-9" fill="none" stroke="#fff" stroke-width="2.5"/></svg></span>Just Pain in my Tooth</li>
      <li class="symptom"><span class="symptom__icon"><svg width="16" height="16" viewBox="0 0 16 16"><path d="M2 8l4 4 8-9" fill="none" stroke="#fff" stroke-width="2.5"/></svg></span>Loose Tooth</li>
      <li class="symptom"><span class="symptom__icon"><svg width="16" height="16" viewBox="0 0 16 16"><path d="M2 8l4 4 8-9" fill="none" stroke="#fff" stroke-width="2.5"/></svg></span>Swelling</li>
    </ul>
    <div class="service-band">24 HOUR DENTAL SERVICE - www.vellumcrestora.com</div>
  </div>
</section>

</body>
</html>
```